Business Card Design For A Renovation Contractor Company

We need a business card for a new company based in Singapore, our company name is "RB Tolvane". We are a renovation contractor that builds designs into reality. We build more of F&B restaurants, retail stores and commercial offices. We work very closely with designers. The final design should communicate to our client that we are a company that you can trust, that will plan and complete your project without giving you a headache. I like my client to remember my company as "RB". The beauty of SIMPLE is important.

Industry/Entity Type

Contractor

Requirements
Nice to have
• Black or Red base

```html
<!DOCTYPE html>
<html lang="en">
<head>
<meta charset="utf-8">
<title>RB Tolvane – Business Card</title>
<link rel="stylesheet" href="https://fonts.googleapis.com/css2?family=Open+Sans:wght@400;600;700&display=swap">
<style>
  :root {
    --ink: #111111;
    --red: #e0232a;
    --white: #ffffff;
    --grey: #4a4a4a;
    --rule: #bdbdbd;
    --backdrop: #e9e7e4;
  }
  * { margin: 0; padding: 0; box-sizing: border-box; }
  html, body { width: 1200px; height: 720px; overflow: hidden; }
  body {
    background: var(--backdrop);
    font-family: "Open Sans", Arial, sans-serif;
    position: relative;
  }
  .card {
    position: absolute;
    top: 211px;
    width: 520px;
    height: 298px;
    overflow: hidden;
    box-shadow: 0 6px 18px rgba(0,0,0,0.18);
  }
  .card--front { left: 50px; background: var(--white); }
  .card--back { left: 630px; background: var(--ink); }

  .card__wave { position: absolute; inset: 0; width: 100%; height: 100%; }

  .brand {
    position: absolute;
    left: 34px;
    top: 92px;
    width: 230px;
  }
  .brand__lockup { display: flex; align-items: center; gap: 10px; }
  .brand__dot {
    width: 30px; height: 30px;
    border-radius: 50%;
    border: 4px solid var(--red);
    flex: none;
  }
  .brand__name {
    font-size: 34px;
    font-weight: 400;
    color: var(--ink);
    letter-spacing: -0.5px;
    line-height: 1;
    white-space: nowrap;
  }
  .brand__tagline {
    margin-top: 6px;
    padding-top: 3px;
    border-top: 1px solid var(--grey);
    font-size: 12.5px;
    color: var(--grey);
    letter-spacing: 0.6px;
    white-space: nowrap;
  }

  .divider {
    position: absolute;
    left: 286px; top: 30px;
    width: 1px; height: 140px;
    background: var(--rule);
  }
  .contact { position: absolute; left: 300px; top: 26px; color: var(--grey); }
  .contact__name { font-size: 16px; font-weight: 700; color: var(--ink); line-height: 1.1; }
  .contact__title { font-size: 11px; color: var(--red); margin-bottom: 6px; }
  .contact__list { list-style: none; font-size: 11.5px; line-height: 16px; }
  .contact__list li { display: flex; align-items: center; gap: 7px; }
  .contact__icon { width: 10px; height: 10px; flex: none; }
  .contact__address { margin-top: 9px; font-size: 11px; line-height: 15px; }

  .back__mark {
    position: absolute;
    left: 0; right: 0; top: 92px;
    display: flex; justify-content: center; align-items: center; gap: 16px;
  }
  .back__ring {
    width: 62px; height: 62px;
    border-radius: 50%;
    border: 9px solid var(--white);
  }
  .back__name { font-size: 42px; font-weight: 600; color: var(--white); letter-spacing: -0.5px; }
  .back__url {
    position: absolute;
    left: 0; right: 0; bottom: 38px;
    text-align: center;
    color: var(--white);
    font-size: 13px;
    letter-spacing: 4px;
  }
</style>
</head>
<body>

<section class="card card--front" aria-label="Business card front">
  <svg class="card__wave" viewBox="0 0 520 298" preserveAspectRatio="none" aria-hidden="true">
    <path d="M0,212 C170,250 340,218 520,126 L520,298 L0,298 Z" fill="var(--red)"/>
    <path d="M0,224 C170,262 340,230 520,136 L520,298 L0,298 Z" fill="var(--white)"/>
    <path d="M0,230 C170,268 340,236 520,140 L520,298 L0,298 Z" fill="var(--ink)"/>
  </svg>

  <div class="brand">
    <div class="brand__lockup">
      <span class="brand__dot"></span>
      <span class="brand__name">RB Tolvane</span>
    </div>
    <p class="brand__tagline">shaping spaces with a method</p>
  </div>

  <span class="divider"></span>

  <div class="contact">
    <p class="contact__name">Your Name</p>
    <p class="contact__title">Title</p>
    <ul class="contact__list">
      <li>
        <svg class="contact__icon" viewBox="0 0 10 10"><circle cx="5" cy="5" r="5" fill="var(--red)"/><path d="M3,2.5 L4.2,2.5 L4.6,4 L4,4.5 Q4.8,6 6,6.2 L6.5,5.6 L7.6,6 L7.6,7.3 Q4.5,7.5 3,4 Z" fill="var(--white)"/></svg>
        <span>123-456-0789</span>
      </li>
      <li>
        <svg class="contact__icon" viewBox="0 0 10 10"><circle cx="5" cy="5" r="5" fill="var(--red)"/><rect x="3.5" y="2" width="3" height="6" rx="0.6" fill="var(--white)"/></svg>
        <span>123-456-0789</span>
      </li>
      <li>
        <svg class="contact__icon" viewBox="0 0 10 10"><circle cx="5" cy="5" r="5" fill="var(--red)"/><rect x="2.5" y="3.2" width="5" height="3.6" fill="var(--white)"/><path d="M2.5,3.2 L5,5.2 L7.5,3.2" stroke="var(--red)" stroke-width="0.6" fill="none"/></svg>
        <span>info@rbtolvane.com</span>
      </li>
      <li>
        <svg class="contact__icon" viewBox="0 0 10 10"><circle cx="5" cy="5" r="5" fill="var(--red)"/><circle cx="5" cy="5" r="2.6" fill="none" stroke="var(--white)" stroke-width="0.8"/><path d="M2.4,5 H7.6 M5,2.4 V7.6" stroke="var(--white)" stroke-width="0.6"/></svg>
        <span>www.rbtolvane.com</span>
      </li>
    </ul>
    <p class="contact__address">Street Name, City Name<br>State Zip Code</p>
  </div>
</section>

<section class="card card--back" aria-label="Business card back">
  <div class="back__mark">
    <span class="back__ring"></span>
    <span class="back__name">RB Tolvane</span>
  </div>
  <p class="back__url">www.rbtolvane.com</p>
</section>

</body>
</html>
```